Webdesign für Personalvermittlung
Zielgruppe
Personalvermittlung
Aufgabenstellung
es soll einladend - nicht zu überladen und natürlich cool und modern sein

```html
<!DOCTYPE html>
<html lang="de">
<head>
<meta charset="utf-8">
<title>pflegeweg job – Personalvermittlung Pflege</title>
<link rel="stylesheet" href="https://fonts.googleapis.com/css2?family=Raleway:ital,wght@0,400;0,500;0,600;0,700;0,800;0,900;1,400;1,500;1,600;1,700;1,800&family=Lato:ital,wght@0,400;0,700;1,400;1,700&display=swap">
<style>
:root{
  --orange:#f7931e;
  --blue:#29a9e1;
  --blue-line:#3a8fd0;
  --sky:#d9f0fb;
  --ink:#1d1d1d;
  --footer:#221c30;
  --white:#ffffff;
}
*{box-sizing:border-box;margin:0;padding:0}
html,body{width:1200px;height:4413px;overflow:hidden;background:var(--white)}
body{font-family:"Raleway",sans-serif;color:var(--ink)}
.page{position:relative;width:1200px;height:4413px;overflow:hidden}
.abs{position:absolute}

.brand{left:82px;top:14px;width:130px;text-align:center}
.brand-mark{width:50px;height:50px;border-radius:50%;background:var(--blue);margin:0 auto 6px}
.brand-name{font-weight:600;font-size:19px;color:var(--ink)}
.top-question{left:648px;top:41px;font-size:12px;color:var(--ink)}
.top-phone{left:798px;top:40px;font-size:13px;font-weight:700;color:var(--blue);display:flex;gap:6px;align-items:center}
.btn{display:flex;align-items:center;justify-content:center;background:var(--orange);color:var(--white);font-weight:700;text-transform:uppercase;border-radius:4px}
.btn-apply{left:966px;top:31px;width:152px;height:37px;font-size:16px;gap:8px}

.nav{left:0;top:108px;width:1200px;height:58px;background:var(--blue)}
.nav a{position:absolute;top:0;height:58px;line-height:58px;color:var(--white);font-size:20px;font-weight:600;text-decoration:none}
.nav .active{left:81px;width:156px;background:var(--orange);text-align:center}

.hero{left:0;top:166px;width:1200px;height:737px;background:linear-gradient(100deg,#4eb4e2 0%,#7cc9ea 45%,#bfe3f2 70%,#8fcbe6 100%)}
.hero-deco-1{left:1128px;top:170px;width:150px;height:150px;border-radius:50%;background:#55b9e6}
.hero-deco-2{left:-85px;top:725px;width:162px;height:162px;border-radius:50%;background:#55b9e6}
.hero-title{left:103px;top:328px;font-weight:900;font-size:58px;line-height:67px;color:var(--white);letter-spacing:-.5px;text-shadow:0 2px 4px rgba(0,0,0,.2)}
.hero-title span{color:var(--orange)}
.hero-sub{left:103px;top:548px;font-weight:700;font-size:29px;line-height:42px;color:#1c1c1c}
.btn-offer{left:101px;top:708px;width:233px;height:54px;font-size:16px}
.dots{left:765px;top:849px;display:flex;gap:12px}
.dots i{display:block;width:87px;height:11px;border-radius:6px;background:#dcdcdc}
.dots i.on{background:var(--blue)}

.offer{left:0;top:953px;width:1200px;height:610px;background:var(--sky)}
.offer-circle{left:94px;top:953px;width:180px;height:90px;border-radius:0 0 90px 90px;background:#8fd0ee}
.offer-title{left:89px;top:976px;font-weight:500;font-size:35px;line-height:41px;color:var(--orange);width:400px}
.offer-rule{left:89px;top:1109px;width:398px;height:2px;background:var(--blue-line)}
.you-are{left:86px;top:1126px;font-style:italic;font-weight:600;font-size:19px}
.roles{left:88px;top:1164px;list-style:none}
.roles li{display:flex;align-items:center;gap:30px;height:53.5px;font-style:italic;font-size:19px}
.video{left:587px;top:983px;width:529px;height:312px;border-radius:16px;background:#8fc7e6;padding:20px}
.video-inner{width:100%;height:100%;border-radius:12px;background:linear-gradient(110deg,#1d5fb2,#6aa4d6 60%,#c9dbe8)}
.offer-text{left:612px;top:1366px;width:520px;font-style:italic;font-weight:700;font-size:19px;line-height:25px}
.offer-text p+p{margin-top:22px}
.btn-wir{left:611px;top:1494px;width:241px;height:50px;font-size:16px;border-radius:2px}

.expect-title{left:0;top:1612px;width:1200px;text-align:center;font-weight:500;font-size:35px;line-height:41px;color:var(--orange)}
.expect-rule{left:289px;top:1706px;width:624px;height:2px;background:var(--blue-line)}
.expect-sub{left:0;top:1724px;width:1200px;text-align:center;font-style:italic;font-weight:500;font-size:20px;color:#444}
.backdrop{left:378px;top:1800px;width:408px;height:660px;border-radius:48px;background:linear-gradient(180deg,#e4e4e4,#d6d6d6)}
.feat h3{font-weight:600;font-size:25px;line-height:35px;color:var(--orange)}
.feat p{font-size:14.5px;line-height:26.3px;color:#444;margin-top:14px}
.feat p b{color:var(--orange)}
.ico{width:48px;height:48px}

.about{left:0;top:2545px;width:1198px;height:413px;background:var(--sky)}
.about h2{position:absolute;left:0;top:42px;width:1158px;text-align:center;font-weight:500;font-size:34px;color:var(--orange)}
.about .rule{position:absolute;left:251px;top:106px;width:625px;height:2px;background:var(--blue-line)}
.about .sub{position:absolute;left:0;top:120px;width:1158px;text-align:center;font-style:italic;font-weight:500;font-size:20px;color:#444}
.about .txt{position:absolute;left:150px;top:183px;width:900px;text-align:center;font-style:italic;font-size:14.5px;line-height:26px;color:#333}
.btn-weiter{left:484px;top:2862px;width:204px;height:50px;font-size:16px;border-radius:2px}

.quote-deco{left:1000px;top:2950px;font-weight:900;font-size:150px;line-height:1;color:#e9f2f7}
.form{left:103px;top:3022px;width:555px}
.form h2{font-weight:600;font-size:32px;line-height:37px;color:var(--orange)}
.form .callback{margin-top:22px;font-style:italic;font-size:14px;color:#666;padding-bottom:6px;border-bottom:1px solid #ddd}
.fld label{display:block;font-style:italic;font-size:13px;color:#222;margin-bottom:8px}
.field{border:1px solid #d8d8d8;background:var(--white);font-style:italic;font-size:12px;color:#aaa;padding:0 13px;display:flex;align-items:center}
.field.focus{border-color:#3a7bd5}
.field.area{align-items:flex-start;padding-top:16px}
.btn-send{left:103px;top:3527px;width:554px;height:51px;font-size:16px;border-radius:2px}

.card{left:694px;top:3013px;width:500px;height:642px;background:var(--sky);border-radius:6px;overflow:hidden}
.card h2{position:absolute;left:17px;top:28px;font-weight:700;font-size:35px;color:var(--orange)}
.card .lbl{position:absolute;left:17px;font-style:italic;font-size:27px;color:#333}
.card .portrait{position:absolute;left:18px;top:130px;width:137px;height:137px;background:linear-gradient(160deg,#c9d4dc,#4e5a66)}
.card .name{position:absolute;left:25px;top:293px;font-style:italic;font-weight:800;font-size:28px;color:#1a1a1a}
.card .row{position:absolute;left:24px;display:flex;gap:18px;align-items:flex-start;font-style:italic;font-weight:700;font-size:17px;color:#1a1a1a;line-height:20px}
.card .corner{position:absolute;left:410px;top:560px;width:180px;height:180px;border-radius:50%;background:var(--orange)}

.map{left:5px;top:3690px;width:1190px;height:393px;background:linear-gradient(135deg,#eef0ee,#e3e6e4 50%,#dfe7df)}

.footer{left:0;top:4137px;width:1200px;height:213px;background:var(--footer)}
.footer .fbrand{position:absolute;left:104px;top:16px;width:200px;text-align:center}
.footer .fmark{width:74px;height:74px;border-radius:50%;background:#7a5ad6;margin:0 auto 10px}
.footer .fname{font-weight:600;font-size:27px;color:var(--white)}
.footer .social{display:flex;gap:13px;justify-content:center;margin-top:14px}
.footer .social i{display:block;width:22px;height:22px;background:#dfe4ee}
.footer h4{position:absolute;top:14px;font-style:italic;font-weight:400;font-size:19px;color:#d0d0d0}
.footer ul{position:absolute;left:436px;top:84px;list-style:disc;color:#ccc;font-style:italic;font-size:12px;line-height:18px;padding-left:12px}
.footer .sub-box{position:absolute;left:795px;top:72px;width:329px;height:46px;background:var(--white);display:flex;align-items:center;gap:12px;padding-left:14px;font-size:13px;color:#888}
.footer .note{position:absolute;left:795px;top:135px;width:330px;font-style:italic;font-size:12px;line-height:18px;color:#ccc}
.copy{left:0;top:4372px;width:1200px;text-align:center;font-size:13px;color:#333}
</style>
</head>
<body>
<div class="page">

  <div class="abs brand"><div class="brand-mark"></div><div class="brand-name">pflegeweg job</div></div>
  <div class="abs top-question">Any Qirgendeine Frage</div>
  <div class="abs top-phone">
    <svg width="14" height="14" viewBox="0 0 24 24"><path fill="#29a9e1" d="M6.6 10.8a15 15 0 0 0 6.6 6.6l2.2-2.2a1 1 0 0 1 1-.25 11.4 11.4 0 0 0 3.6.57 1 1 0 0 1 1 1V20a1 1 0 0 1-1 1A17 17 0 0 1 3 4a1 1 0 0 1 1-1h3.5a1 1 0 0 1 1 1c0 1.25.2 2.45.57 3.57a1 1 0 0 1-.25 1z"/></svg>
    07100 555 123 4
  </div>
  <div class="abs btn btn-apply">
    <svg width="16" height="16" viewBox="0 0 24 24"><path fill="none" stroke="#fff" stroke-width="2.2" d="M4 20h4L19 9l-4-4L4 16z"/></svg>Anwenden
  </div>

  <nav class="abs nav">
    <a class="active" href="#">Home</a>
    <a href="#" style="left:295px">Wir Bieten Dir</a>
    <a href="#" style="left:540px">Uber Uns</a>
    <a href="#" style="left:764px">Kontakt</a>
  </nav>

  <div class="abs hero" role="img" aria-label="Foto einer lächelnden Pflegekraft in blauer Dienstkleidung"></div>
  <div class="abs hero-deco-1"></div>
  <div class="abs hero-deco-2"></div>
  <svg class="abs" style="left:58px;top:466px" width="24" height="40" viewBox="0 0 24 40"><path d="M20 4 4 20l16 16" fill="none" stroke="#fff" stroke-width="3"/></svg>
  <svg class="abs" style="left:1132px;top:466px" width="24" height="40" viewBox="0 0 24 40"><path d="M4 4l16 16L4 36" fill="none" stroke="#fff" stroke-width="3"/></svg>
  <h1 class="abs hero-title">DEIN NÄCHSTER<br>KARRIERESCHRITT IM<br><span>PFLEGEBERUF!</span></h1>
  <p class="abs hero-sub">Wir bieten Ihnen den perfekten<br>Job als Führungskraft!</p>
  <div class="abs btn btn-offer">Ich will ein Angebot!</div>
  <div class="abs dots"><i></i><i class="on"></i><i></i><i></i></div>

  <section class="abs offer"></section>
  <div class="abs offer-circle"></div>
  <h2 class="abs offer-title">Wir bieten Ihnen<br>den perfekten<br>Job als Führungskraft!</h2>
  <div class="abs offer-rule"></div>
  <div class="abs you-are">Du bist:</div>
  <ul class="abs roles">
    <li><svg width="26" height="20" viewBox="0 0 26 20"><path d="M2 10l7 7L24 2" fill="none" stroke="#27a844" stroke-width="4"/></svg>Wohnbereichsleiter/in</li>
    <li><svg width="26" height="20" viewBox="0 0 26 20"><path d="M2 10l7 7L24 2" fill="none" stroke="#27a844" stroke-width="4"/></svg>Pflegedienstleiter/in</li>
    <li><svg width="26" height="20" viewBox="0 0 26 20"><path d="M2 10l7 7L24 2" fill="none" stroke="#27a844" stroke-width="4"/></svg>Stationsleiter/in</li>
    <li><svg width="26" height="20" viewBox="0 0 26 20"><path d="M2 10l7 7L24 2" fill="none" stroke="#27a844" stroke-width="4"/></svg>OP-Manager/in</li>
    <li><svg width="26" height="20" viewBox="0 0 26 20"><path d="M2 10l7 7L24 2" fill="none" stroke="#27a844" stroke-width="4"/></svg>Heimleiter/in</li>
    <li><svg width="26" height="20" viewBox="0 0 26 20"><path d="M2 10l7 7L24 2" fill="none" stroke="#27a844" stroke-width="4"/></svg>Klinikdirektor/in</li>
  </ul>
  <div class="abs video"><div class="video-inner" role="img" aria-label="Vorschaubild eines Willkommensvideos mit Ärzteteam"></div></div>
  <div class="abs offer-text">
    <p>und willst Dich verändern? Oder möchtest eine Weiterbildung in die Management-Ebene?</p>
    <p>Dann nimm Kontakt zu uns auf...</p>
  </div>
  <div class="abs btn btn-wir">Wir bieten Dir</div>

  <h2 class="abs expect-title">Was darfst Du von<br>PFLEGEWEG-JOB.de erwarten?</h2>
  <div class="abs expect-rule"></div>
  <div class="abs expect-sub">Ihr Erfolg, unser Engagement</div>
  <div class="abs backdrop" role="img" aria-label="Hellgraue Landkarte als dezenter Hintergrund"></div>

  <div class="abs" style="left:98px;top:1800px">
    <svg class="ico" viewBox="0 0 48 48"><rect x="4" y="14" width="40" height="28" rx="3" fill="#f7931e"/><rect x="17" y="7" width="14" height="8" rx="2" fill="none" stroke="#d2541b" stroke-width="3"/><rect x="4" y="24" width="40" height="3" fill="#d2541b"/></svg>
  </div>
  <div class="abs feat" style="left:172px;top:1790px;width:245px">
    <h3>Zugriff auf mehr<br>Stellen</h3>
    <p>In Zusammenarbeit mit Einrichtungen und Kliniken erhalten unsere Kandidaten einen zugesicherten Bonus in Höhe von 750 EUR für das Vertrauen bei Ihrem Jobwechsel in pflegeweg-job.de</p>
  </div>

  <div class="abs" style="left:438px;top:1808px"><svg width="60" height="40" viewBox="0 0 60 40"><path d="M2 6h44l8 8-8 8H2z" fill="#f7931e"/><path d="M50 20c6 6 0 14-8 12" fill="none" stroke="#333" stroke-width="2"/></svg></div>
  <div class="abs feat" style="left:523px;top:1800px;width:255px">
    <h3>100% kostenfrei</h3>
    <p>Unsere Dienstleistung ist für Dich als Bewerber 100% kostenfrei! Es gibt auch garantiert keine versteckten Kosten!</p>
  </div>

  <div class="abs" style="left:782px;top:1805px"><svg width="48" height="28" viewBox="0 0 48 28"><path d="M14 4a10 10 0 1 0 0 20c10 0 10-20 20-20a10 10 0 1 1 0 20C24 24 24 4 14 4z" fill="none" stroke="#f7931e" stroke-width="5"/></svg></div>
  <div class="abs feat" style="left:874px;top:1798px;width:240px">
    <h3>Dauerhafte<br>Betreuung</h3>
    <p>Dein neuer Arbeitgeber hält nicht was er verspricht? Keine Sorge, wir werden für Dich sofort wieder aktiv und bieten Dir schnell neue Möglichkeiten an - ohne dass Du erneut Bewerbungen versenden musst! Ein Anruf oder eine Email genügt!</p>
  </div>

  <div class="abs" style="left:92px;top:2158px"><svg class="ico" viewBox="0 0 48 48"><path d="M8 4h24l8 8v32H8z" fill="none" stroke="#f7931e" stroke-width="3"/><path d="M14 18h18M14 25h18M14 32h12" stroke="#f7931e" stroke-width="3"/></svg></div>
  <div class="abs feat" style="left:171px;top:2150px;width:245px">
    <h3>Alle<br>Versprechungen<br>findest Du im<br>Arbeitsvertrag</h3>
    <p>In Zusammenarbeit mit Einrichtungen und Kliniken erhalten unsere Kandidaten einen zugesicherten Bonus in Höhe von 750 EUR für das Vertrauen bei Ihrem Jobwechsel in pflegeweg-job.de</p>
  </div>

  <div class="abs" style="left:438px;top:2160px"><svg class="ico" viewBox="0 0 48 48"><path d="M4 24c8-12 32-12 40 0-8 12-32 12-40 0z" fill="none" stroke="#f7931e" stroke-width="4"/><circle cx="24" cy="24" r="6" fill="#f7931e"/><path d="M8 8l32 32" stroke="#f7931e" stroke-width="4"/></svg></div>
  <div class="abs feat" style="left:523px;top:2162px;width:255px">
    <h3>Anonymität</h3>
    <p>Wir erstellen ein Profil Deiner Kenntnisse und Fähigkeiten sowie Deiner Berufserfahrung. Weder Dein Name, noch Deine Vorarbeitgeber tauchen im ersten Schritt auf. Erst wenn eine Einrichtung oder Klinik daran Interesse zeigt, entscheiden wir gemeinsam, wie es weitergeht!</p>
  </div>

  <div class="abs" style="left:782px;top:2160px"><svg class="ico" viewBox="0 0 48 48"><circle cx="24" cy="20" r="12" fill="#f7931e"/><rect x="10" y="34" width="28" height="10" rx="5" fill="#f2b84b"/></svg></div>
  <div class="abs feat" style="left:877px;top:2162px;width:240px">
    <h3>Keine Zeitarbeit</h3>
    <p>Wir vermitteln ausschließlich in Festanstellungen direkt bei Kliniken oder Einrichtungen. Wir können Dir jedoch wertvolle Tipps geben , sollte Zeitarbeit für Dich in Frage kommen ...<b>WIR KENNEN UNS AUS!</b></p>
  </div>

  <section class="abs about">
    <h2>ÜBER UNS</h2>
    <div class="rule"></div>
    <div class="sub">Ihr Erfolg, unser Engagement</div>
    <p class="txt">PFLEGEWEG-JOB.de hat es sich mit über 15 Jahren Erfahrung zum Ziel gesetzt, Fachkräften im Gesundheitswesen dabei zu helfen, lohnende Führungspositionen zu finden. Wir sind darauf spezialisiert, qualifizierte Kandidaten mit erstklassigen Gesundheitseinrichtungen zusammenzubringen.</p>
  </section>
  <div class="abs btn btn-weiter">Weiter</div>

  <div class="abs quote-deco">”</div>
  <div class="abs form">
    <h2>Nimm ganz einfach Kontakt zu uns auf:</h2>
    <div class="callback">gewünschter Rückruf-Zeitpunkt</div>
  </div>
  <div class="abs fld" style="left:103px;top:3203px"><label>Nachname</label><div class="field" style="width:264px;height:44px">Gib deinen Namen ein</div></div>
  <div class="abs fld" style="left:393px;top:3203px"><label>E-Mail-Adresse</label><div class="field focus" style="width:264px;height:44px">John.exp@gml</div></div>
  <div class="abs fld" style="left:103px;top:3290px"><label>Betreff</label><div class="field area" style="width:554px;height:66px">Geben Sie Ihre Anforderung ein...</div></div>
  <div class="abs fld" style="left:103px;top:3401px"><label>Nachricht</label><div class="field area" style="width:554px;height:66px">Was möchten Sie vermitteln?</div></div>
  <div class="abs btn btn-send">Senden</div>

  <aside class="abs card">
    <div class="corner"></div>
    <h2>KONTAKTDATEN</h2>
    <div class="lbl" style="top:85px">Ansprechpartner</div>
    <div class="portrait" role="img" aria-label="Porträtfoto des Ansprechpartners"></div>
    <div class="name">Herr Lukas Brenner</div>
    <div class="row" style="top:342px"><svg width="20" height="20" viewBox="0 0 24 24"><path fill="#f7931e" d="M6.6 10.8a15 15 0 0 0 6.6 6.6l2.2-2.2a1 1 0 0 1 1-.25 11.4 11.4 0 0 0 3.6.57 1 1 0 0 1 1 1V20a1 1 0 0 1-1 1A17 17 0 0 1 3 4a1 1 0 0 1 1-1h3.5a1 1 0 0 1 1 1c0 1.25.2 2.45.57 3.57a1 1 0 0 1-.25 1z"/></svg>07100 555 123 4</div>
    <div class="row" style="top:390px"><svg width="20" height="20" viewBox="0 0 24 24"><rect x="2" y="5" width="20" height="14" rx="2" fill="#f7931e"/><path d="M3 6l9 7 9-7" fill="none" stroke="#fff" stroke-width="2"/></svg><u>Lukas.brenner@pflegeweg-job.de</u></div>
    <div class="lbl" style="top:440px;left:15px">Adresse:</div>
    <div class="row" style="top:494px"><svg width="22" height="22" viewBox="0 0 24 24"><path fill="#f7931e" d="M12 2a7 7 0 0 0-7 7c0 5 7 13 7 13s7-8 7-13a7 7 0 0 0-7-7zm0 9.5A2.5 2.5 0 1 1 12 6.5a2.5 2.5 0 0 1 0 5z"/></svg>Gewerbehof Linde 7, 76000<br>Musterstadt</div>
    <div class="row" style="top:550px"><svg width="20" height="20" viewBox="0 0 24 24"><path fill="#f7931e" d="M6.6 10.8a15 15 0 0 0 6.6 6.6l2.2-2.2a1 1 0 0 1 1-.25 11.4 11.4 0 0 0 3.6.57 1 1 0 0 1 1 1V20a1 1 0 0 1-1 1A17 17 0 0 1 3 4a1 1 0 0 1 1-1h3.5a1 1 0 0 1 1 1c0 1.25.2 2.45.57 3.57a1 1 0 0 1-.25 1z"/></svg>07100 555 123 4</div>
    <div class="row" style="top:598px"><svg width="20" height="20" viewBox="0 0 24 24"><rect x="2" y="5" width="20" height="14" rx="2" fill="#f7931e"/><path d="M3 6l9 7 9-7" fill="none" stroke="#fff" stroke-width="2"/></svg><u>info@pflegeweg-job.de</u></div>
  </aside>

  <div class="abs map" role="img" aria-label="Straßenkarte mit Standortmarkierung des Büros"></div>

  <footer class="abs footer">
    <div class="fbrand">
      <div class="fmark"></div>
      <div class="fname">pflegeweg job</div>
      <div class="social"><i></i><i></i><i></i><i></i></div>
    </div>
    <h4 style="left:428px">Seitenverzeichnis</h4>
    <ul><li>HOME</li><li>WIR BIETEN DIR</li><li>ÜBER UNS</li><li>KONTAKT</li></ul>
    <h4 style="left:795px">Abonnieren</h4>
    <div class="sub-box">
      <svg width="18" height="14" viewBox="0 0 24 18"><rect x="1" y="1" width="22" height="16" rx="2" fill="none" stroke="#f7931e" stroke-width="2"/><path d="M2 2l10 8 10-8" fill="none" stroke="#f7931e" stroke-width="2"/></svg>
      Geben sie ihre E-Mail Adresse ein
    </div>
    <p class="note">Senden Sie eine E-Mail und Sie erhalten regelmäßig unsere Newsletter, Service-Blogs und Pressemitteilungen</p>
  </footer>
  <div class="abs copy">Copyright 2024 pflegeweg-job.de, All Right Reserved</div>

</div>
</body>
</html>
```